Book about Ice Dragons

I would like a book cover made for my book i am planning on releasing soon, the book is title "Volmera: DUSK", i would like a white background with the words Volmera: DUSK in the middle with some sort of dragon medallion / logo in the middle, i would love the wording to have a subtle ice effect, on the back i want a small picture at the top with a a dragon perched on a rock with a man standing below the dragon, I want the dragon to dwarf the man, I like the stronger dinosaur like dragons not the Chinese style. I really like the way the dragon looks in the attached picture but i'm not a fan of the whiskers on the dragons face.

```html
<!DOCTYPE html>
<html lang="en">
<head>
<meta charset="utf-8">
<title>Volmera: DUSK — Book Cover</title>
<link href="https://fonts.googleapis.com/css2?family=Cinzel:wght@600&family=Uncial+Antiqua&display=swap" rel="stylesheet">
<style>
  :root {
    --page-bg: #ffffff;
    --cover-base: #ddd6d9;
    --cover-light: #ece7e9;
    --cover-shade: #cdc5c9;
    --author-ink: #141212;
    --ice-light: #f4f7fb;
    --ice-mid: #a3abc6;
    --ice-deep: #3c4360;
    --medallion-blue: #8ea5c6;
    --medallion-edge: #7d7f93;
  }
  * { margin: 0; padding: 0; box-sizing: border-box; }
  html, body {
    width: 1200px;
    height: 1013px;
    overflow: hidden;
    background: var(--page-bg);
  }
  .canvas {
    position: relative;
    width: 1200px;
    height: 1013px;
    display: flex;
    align-items: center;
    justify-content: center;
  }
  .cover {
    position: relative;
    width: 490px;
    height: 950px;
    background:
      radial-gradient(ellipse at 30% 20%, var(--cover-light) 0%, transparent 55%),
      radial-gradient(ellipse at 75% 70%, var(--cover-light) 0%, transparent 50%),
      linear-gradient(180deg, var(--cover-base) 0%, var(--cover-shade) 100%);
    box-shadow: 0 10px 30px rgba(0, 0, 0, 0.12);
    overflow: hidden;
  }
  .author {
    position: absolute;
    top: 86px;
    left: 0;
    width: 100%;
    text-align: center;
    font-family: "Cinzel", serif;
    font-weight: 600;
    font-size: 46px;
    line-height: 1;
    letter-spacing: 0.5px;
    color: var(--author-ink);
  }
  .medallion {
    position: absolute;
    top: 300px;
    left: 62px;
    width: 300px;
    height: 320px;
    border-radius: 50%;
    background: radial-gradient(circle at 55% 48%, var(--medallion-blue) 0%, #9fb2cd 50%, var(--medallion-edge) 78%, rgba(125, 127, 147, 0) 100%);
  }
  .title {
    position: absolute;
    top: 640px;
    left: 0;
    width: 100%;
    text-align: center;
    font-family: "Uncial Antiqua", serif;
    font-weight: 400;
    font-size: 84px;
    line-height: 1.12;
  }
  .title-line {
    display: inline-block;
    background: linear-gradient(180deg, var(--ice-light) 0%, var(--ice-mid) 40%, var(--ice-deep) 58%, var(--ice-mid) 78%, var(--ice-light) 100%);
    -webkit-background-clip: text;
    background-clip: text;
    color: transparent;
    filter: drop-shadow(1px 2px 1px rgba(40, 45, 70, 0.45));
  }
</style>
</head>
<body>
  <main class="canvas">
    <section class="cover">
      <h2 class="author">Callum Reyes</h2>
      <div class="medallion" role="img" aria-label="Winged bronze dragon coiled around an icy blue round medallion"></div>
      <h1 class="title">
        <span class="title-line">Volmera:</span><br>
        <span class="title-line">DUSK</span>
      </h1>
    </section>
  </main>
</body>
</html>
```